Chimney Service company needs new business card design

We need a updated business card with our new logo added. We provide a full range of chimney services throughout Vermont and New Hampshire. The business card will be one sided and color. Attached is our current business card another document showing all the information we would like on the card.
We dont like a lot of flashy colors.... here is a link to our website to get an idea of our branding www.flueguardianvt.example

Target Market(s)

homeowners

Industry/Entity Type

Business

Contact Information for Business Card

See attached sheet for content.

Font styles to use
Serif
Sans Serif

Requirements
Must have
• all information provided on separate sheet
Should not have
• Additional information that may clogg up design

```html
<!DOCTYPE html>
<html lang="en">
<head>
<meta charset="utf-8">
<title>Flue Guardian — Business Card</title>
<link rel="stylesheet" href="https://fonts.googleapis.com/css2?family=Bebas+Neue&family=Roboto:wght@400&display=swap">
<style>
  :root {
    --backdrop: #1f1f1f;
    --brand-panel: #eeeeee;
    --info-panel: #2c2c2c;
    --ink-dark: #2a2a2a;
    --ink-light: #f2f2f2;
    --rule-light: #9a9a9a;
  }
  * { box-sizing: border-box; margin: 0; padding: 0; }
  html, body {
    width: 1200px; height: 871px; overflow: hidden;
    background: var(--backdrop);
  }
  .business-card {
    position: absolute;
    left: 260px; top: 241px;
    width: 680px; height: 388px;
    display: flex;
    box-shadow: 0 6px 18px rgba(0,0,0,.45);
  }
  .brand-panel {
    position: relative;
    width: 205px; height: 100%;
    background: var(--brand-panel);
  }
  .brand-name {
    position: absolute;
    left: 76px; top: 36px;
    height: 250px;
    writing-mode: vertical-rl;
    transform: rotate(180deg);
    font-family: "Roboto", sans-serif;
    font-weight: 400;
    font-size: 27px;
    letter-spacing: 2.5px;
    color: var(--ink-dark);
    text-align: center;
    line-height: 1;
  }
  .brand-rule {
    position: absolute;
    left: 114px; top: 36px;
    width: 2px; height: 250px;
    background: var(--ink-dark);
  }
  .brand-mark {
    position: absolute;
    left: 77px; top: 298px;
    width: 50px; height: 50px;
    background: var(--ink-dark);
  }
  .info-panel {
    flex: 1;
    background: var(--info-panel);
    color: var(--ink-light);
    padding: 44px 0 0 73px;
  }
  .tagline {
    font-family: "Bebas Neue", sans-serif;
    font-size: 22px;
    line-height: 23px;
    letter-spacing: .2px;
  }
  .dotted-rule {
    width: 290px;
    border-top: 2px dotted var(--rule-light);
  }
  .tagline + .dotted-rule { margin-top: 17px; }
  .service-list {
    list-style: none;
    font-family: "Roboto", sans-serif;
    font-size: 16.5px;
    letter-spacing: .4px;
    line-height: 20.4px;
    margin: 19px 0 15px;
  }
  .service-list li::before {
    content: "";
    display: inline-block;
    width: 6px; height: 6px;
    border-radius: 50%;
    background: var(--ink-light);
    margin: 0 15px 3px 1px;
    vertical-align: middle;
  }
  .contact-list {
    list-style: none;
    margin-top: 20px;
    font-family: "Roboto", sans-serif;
    font-size: 16.5px;
    letter-spacing: .4px;
    line-height: 21.5px;
  }
  .contact-list li { display: flex; align-items: center; }
  .contact-icon {
    width: 14px; height: 14px;
    margin-right: 8px;
    fill: var(--ink-light);
  }
</style>
</head>
<body>
  <div class="business-card">
    <div class="brand-panel">
      <div class="brand-name">FLUE GUARDIAN</div>
      <div class="brand-rule"></div>
      <div class="brand-mark"></div>
    </div>
    <div class="info-panel">
      <p class="tagline">Serving VT &amp; New Hampshire since 1989<br>Fully insured — free estimates<br>Family owned &amp; operated</p>
      <div class="dotted-rule"></div>
      <ul class="service-list">
        <li>Full Masonry Services</li>
        <li>Historic chimney restoration</li>
        <li>Stainless steel liners</li>
        <li>New Chimney installations</li>
        <li>FGCI Certified Chimney sweeps</li>
      </ul>
      <div class="dotted-rule"></div>
      <ul class="contact-list">
        <li>
          <svg class="contact-icon" viewBox="0 0 16 16" aria-hidden="true"><path d="M3.6 1.2l2.3 2.9-1.3 1.8c.9 2 2.5 3.6 4.5 4.5l1.8-1.3 2.9 2.3-1.4 2.6C7.3 14 2 8.7 1 3.4z"/></svg>
          802-555-0147
        </li>
        <li>
          <svg class="contact-icon" viewBox="0 0 16 16" aria-hidden="true"><path d="M1 3.5h14v9H1z M1.5 4l6.5 5 6.5-5" stroke="#2c2c2c" stroke-width="1.2"/></svg>
          info@flueguardianvt.example
        </li>
        <li>
          <svg class="contact-icon" viewBox="0 0 16 16" aria-hidden="true"><circle cx="8" cy="8" r="7"/><path d="M1 8h14M8 1c-3 3.5-3 10.5 0 14M8 1c3 3.5 3 10.5 0 14" stroke="#2c2c2c" stroke-width="1.1" fill="none"/></svg>
          www.flueguardianvt.example
        </li>
      </ul>
    </div>
  </div>
</body>
</html>
```